real esate business card with company logo and name

we need a business card design for a real esate company

The company name is Walsh & Brand Pty Ltd, and we have our logo designed and will upload. We want classic or moden feel. Black or white background. looks more textured. Should include folowinginformations
Owen Walsh and Lucy Brand
Sales Agents & Onsite Manager
p: 07 5948 2063
F: 07 5948 2174
M:0431 857 219
3/42 Marlow Crescent, FERNLEA QLD 4213

We want this business card looks professonal. Thank you in advance.

Industry/Entity Type

Real Estate Agent

Contact Information for Business Card

Owen Walsh and Lucy Brand
Onsite Manager & Sales Agents
p: 07 5948 2063
M:0431 857 219

Font styles to use
Serif

Colors
000000
fbfbfb
333333
959595

Requirements
Must have
• company logo and name, black or white back ground

```html
<!DOCTYPE html>
<html lang="en">
<head>
<meta charset="utf-8">
<title>Walsh &amp; Brand Pty Ltd — Business Card</title>
<link rel="stylesheet" href="https://fonts.googleapis.com/css2?family=Roboto+Condensed:wght@400&family=Open+Sans:wght@400&family=Questrial&display=swap">
<style>
  :root {
    --backdrop: #3a3a3a;
    --card-light: #fbfbfb;
    --card-dark: #4a4a4a;
    --ink: #333333;
    --ink-soft: #959595;
    --ink-mid: #666666;
    --white: #ffffff;
  }
  * { margin: 0; padding: 0; box-sizing: border-box; }
  html, body {
    width: 1200px;
    height: 750px;
    overflow: hidden;
    background: var(--backdrop);
  }
  .canvas {
    position: relative;
    width: 1200px;
    height: 750px;
  }
  .card {
    position: absolute;
    top: 228px;
    width: 461px;
    height: 262px;
  }
  .card--front { left: 124px; background: var(--card-light); }
  .card--back  { left: 618px; background: var(--card-dark); }

  .front-tab {
    position: absolute;
    left: 0;
    top: 72px;
    width: 9px;
    height: 29px;
    background: var(--ink);
  }
  .contact {
    position: absolute;
    left: 41px;
    top: 68px;
  }
  .contact__names {
    font-family: "Roboto Condensed", sans-serif;
    font-size: 16px;
    color: var(--ink);
    line-height: 20px;
  }
  .contact__role {
    font-family: "Roboto Condensed", sans-serif;
    font-size: 11.5px;
    color: var(--ink-soft);
    line-height: 16px;
    margin-top: 1px;
  }
  .contact__lines {
    list-style: none;
    margin-top: 9px;
  }
  .contact__line {
    display: flex;
    align-items: center;
    height: 17.5px;
    font-family: "Open Sans", sans-serif;
    font-size: 10.5px;
    color: var(--ink);
  }
  .contact__icon {
    width: 14px;
    height: 12px;
    margin-right: 5px;
    fill: var(--ink);
  }
  .contact__address {
    margin-top: 7px;
    font-family: "Open Sans", sans-serif;
    font-size: 10.5px;
    line-height: 14px;
    color: var(--ink);
    font-style: normal;
  }

  .brand {
    position: absolute;
    display: flex;
    flex-direction: column;
    align-items: center;
    transform: translateX(-50%);
  }
  .card--front .brand { left: 344px; top: 72px; }
  .card--back .brand  { left: 230px; top: 80px; }
  .brand__square {
    width: 58px;
    height: 58px;
    margin-bottom: 24px;
  }
  .card--front .brand__square { background: var(--ink-mid); }
  .card--back .brand__square  { background: var(--white); }
  .brand__name {
    font-family: "Questrial", sans-serif;
    font-size: 11.5px;
    letter-spacing: 0.3px;
    white-space: nowrap;
    text-transform: uppercase;
  }
  .card--front .brand__name { color: var(--ink-mid); }
  .card--back .brand__name  { color: var(--white); }
</style>
</head>
<body>
<main class="canvas">
  <section class="card card--front" aria-label="Business card front">
    <div class="front-tab"></div>
    <div class="contact">
      <h1 class="contact__names">Owen Walsh &amp; Lucy Brand</h1>
      <p class="contact__role">Sales Agents &amp; Onsite Manager</p>
      <ul class="contact__lines">
        <li class="contact__line">
          <svg class="contact__icon" viewBox="0 0 14 12" aria-hidden="true"><path d="M2.2 0.5 4.4 0.2 5.4 3 4 4.1c0.8 1.6 2 2.8 3.6 3.6L8.8 6.3 11.5 7.3 11.3 9.6C11.2 10.4 10.5 11 9.7 10.9 5.2 10.4 1.6 6.8 1.1 2.3 1 1.4 1.4 0.6 2.2 0.5Z"/></svg>
          07 5948 2063
        </li>
        <li class="contact__line">
          <svg class="contact__icon" viewBox="0 0 14 12" aria-hidden="true"><path d="M3.5 0h6a1 1 0 0 1 1 1v11.5a1 1 0 0 1-1 1h-6a1 1 0 0 1-1-1V1a1 1 0 0 1 1-1Zm0.6 1.6v8.6h4.8V1.6Z" transform="scale(0.9)"/></svg>
          0431 857 219
        </li>
        <li class="contact__line">
          <svg class="contact__icon" viewBox="0 0 14 12" aria-hidden="true"><path d="M4 0h6v3H4Zm-3 4h12a1 1 0 0 1 1 1v4H12v3H2V9H0V5a1 1 0 0 1 1-1Zm3 5v2h6V9Z"/></svg>
          07 5948 2174
        </li>
      </ul>
      <address class="contact__address">3/42 Marlow Crescent<br>FERNLEA QLD 4213</address>
    </div>
    <div class="brand">
      <div class="brand__square"></div>
      <p class="brand__name">Walsh &amp; Brand Pty Ltd.</p>
    </div>
  </section>

  <section class="card card--back" aria-label="Business card back">
    <div class="brand">
      <div class="brand__square"></div>
      <p class="brand__name">Walsh &amp; Brand Pty Ltd.</p>
    </div>
  </section>
</main>
</body>
</html>
```